The design should look similar to the uploaded example to accommodate the information needed for a business card template. I would like to see the colors orange and charcoal grey incorporated along with the logo.The following should be on the back of the card SPECIALIZING IN NEW AND USED TIRES & WHEELS FOR:- Loaders- Skid Steers- Telehandlers- Boom Lifts- Forklifs and moreELIMINATING DOWNTIMEWheel Exchange Program for New & Used Foam Filled and Solid Rubber TiresSPECIALTY SERVICES- Foam Filling Tires- Largest Tire Press in SE- ONSITE Forklift Tire Press- Boom Truck Services - Rubber Tracks

Target Market(s)

New and Existing Customers

Industry/Entity Type

Business

Contact Information for Business Card

NAMEHEAVY DUTY TIRE, LLC8470 Belvedere RoadWest Palm Beach, FL 33411P: 844-HD-TIRESF: 561-431-6469C:E: W: WWW.GRANITERIMSUPPLY-EXAMPLE.COM

Font styles to use
Sans Serif

Colors
f37122
333333

Requirements
Must have
• The logo and the information indicated for the backside of the card
Nice to have
• Keep the orange and charcoal grey colors

```html
<!DOCTYPE html>
<html lang="en">
<head>
<meta charset="utf-8">
<title>Granite Rim Supply, LLC – Business Card</title>
<link href="https://fonts.googleapis.com/css2?family=Open+Sans:ital,wght@0,400;0,600;0,700;1,400&family=Roboto+Slab:wght@700&display=swap" rel="stylesheet">
<style>
  :root {
    --orange: #f37122;
    --charcoal: #333333;
    --card-dark: #2f3534;
    --paper: #eeeeef;
    --backdrop: #8f8f8f;
    --ink-soft: #4a4a4a;
    --text-light: #e9e9e9;
    --rule: #c9c9cc;
  }
  * { box-sizing: border-box; margin: 0; padding: 0; }
  html, body { width: 1105px; height: 1200px; overflow: hidden; }
  body {
    background: var(--backdrop);
    font-family: "Open Sans", Arial, sans-serif;
    position: relative;
  }
  .card {
    position: absolute;
    left: 180px;
    width: 746px;
    height: 426px;
  }
  .card--front { top: 119px; background: var(--paper); }
  .card--back  { top: 637px; background: var(--card-dark); color: var(--text-light); text-align: center; }

  /* Front */
  .brand {
    position: absolute;
    left: 66px;
    top: 183px;
    display: flex;
    align-items: center;
    gap: 14px;
  }
  .brand__dot {
    width: 60px; height: 60px;
    border-radius: 50%;
    background: var(--orange);
    flex: none;
  }
  .brand__name {
    font-family: "Roboto Slab", Georgia, serif;
    font-weight: 700;
    font-size: 21px;
    line-height: 1.2;
    color: var(--charcoal);
    text-align: center;
    letter-spacing: 0.5px;
  }
  .divider {
    position: absolute;
    left: 381px; top: 81px;
    width: 1px; height: 284px;
    background: var(--rule);
  }
  .contact {
    position: absolute;
    left: 402px; top: 86px;
    color: var(--ink-soft);
    font-size: 18px;
    line-height: 28px;
    white-space: nowrap;
  }
  .contact__name {
    font-family: "Roboto Slab", Georgia, serif;
    font-weight: 700;
    font-size: 26px;
    line-height: 30px;
    color: var(--charcoal);
    letter-spacing: 0.5px;
  }
  .contact__title {
    font-size: 19px;
    line-height: 24px;
    color: var(--orange);
    font-weight: 600;
    margin-bottom: 14px;
  }
  .contact__address { margin-bottom: 6px; }
  .contact__list { list-style: none; }
  .contact__item { display: flex; align-items: center; gap: 9px; }
  .contact__item svg { width: 17px; height: 17px; fill: var(--charcoal); flex: none; }

  /* Back */
  .back-brand {
    position: absolute;
    left: 0; right: 0; top: 50px;
    display: flex; justify-content: center; align-items: center; gap: 18px;
  }
  .back-brand__dot {
    width: 84px; height: 84px; border-radius: 50%;
    background: var(--orange);
  }
  .back-brand__name {
    font-family: "Roboto Slab", Georgia, serif;
    font-weight: 700;
    font-size: 28px;
    color: var(--text-light);
    letter-spacing: 0.5px;
  }
  .services { position: absolute; left: 0; right: 0; top: 190px; }
  .services__heading {
    font-weight: 600;
    font-size: 19.5px;
    line-height: 28px;
    letter-spacing: 0.3px;
  }
  .services__line {
    font-size: 19.5px;
    line-height: 28px;
  }
  .services__line--italic { font-style: italic; }
  .services__group + .services__group { margin-top: 12px; }
  .dot { color: var(--orange); font-style: normal; padding: 0 3px; }
</style>
</head>
<body>

<section class="card card--front" aria-label="Business card front">
  <div class="brand">
    <span class="brand__dot"></span>
    <p class="brand__name">GRANITE RIM<br>SUPPLY, LLC</p>
  </div>
  <div class="divider"></div>
  <div class="contact">
    <p class="contact__name">DANIEL OKAFOR</p>
    <p class="contact__title">CEO/FOUNDER</p>
    <p class="contact__address">5126 Marston Lane<br>Lake Harlow, FL 33902</p>
    <ul class="contact__list">
      <li class="contact__item">
        <svg viewBox="0 0 24 24" aria-hidden="true"><path d="M6.6 10.8a15.1 15.1 0 0 0 6.6 6.6l2.2-2.2a1 1 0 0 1 1-.25 11.4 11.4 0 0 0 3.6.6 1 1 0 0 1 1 1V20a1 1 0 0 1-1 1A17 17 0 0 1 3 4a1 1 0 0 1 1-1h3.5a1 1 0 0 1 1 1c0 1.25.2 2.45.6 3.6a1 1 0 0 1-.25 1z"/></svg>
        <span>844-GR-WHEEL</span>
      </li>
      <li class="contact__item">
        <svg viewBox="0 0 24 24" aria-hidden="true"><path d="M7 1h10a2 2 0 0 1 2 2v18a2 2 0 0 1-2 2H7a2 2 0 0 1-2-2V3a2 2 0 0 1 2-2zm0 3v14h10V4zm5 15.5a1.2 1.2 0 1 0 0 2.4 1.2 1.2 0 0 0 0-2.4z"/></svg>
        <span>836 512 7740</span>
      </li>
      <li class="contact__item">
        <svg viewBox="0 0 24 24" aria-hidden="true"><path d="M6 2h12v6H6zM3 9h18a2 2 0 0 1 2 2v8h-4v3H5v-3H1v-8a2 2 0 0 1 2-2zm4 8v3h10v-3z"/></svg>
        <span>561-278-9053</span>
      </li>
      <li class="contact__item">
        <svg viewBox="0 0 24 24" aria-hidden="true"><path d="M2 5h20v14H2zm2 2v.5l8 5 8-5V7l-8 5z"/></svg>
        <span>name@graniterim-example.com</span>
      </li>
      <li class="contact__item">
        <svg viewBox="0 0 24 24" aria-hidden="true"><path d="M12 2a10 10 0 1 0 0 20 10 10 0 0 0 0-20zm-1 17.9A8 8 0 0 1 4.1 10L9 15v1a2 2 0 0 0 2 2zm6.9-2.5A2 2 0 0 0 16 16h-1v-3a1 1 0 0 0-1-1H8v-2h2a1 1 0 0 0 1-1V7h2a2 2 0 0 0 2-2v-.4a8 8 0 0 1 2.9 12.8z"/></svg>
        <span>www.graniterimsupply-example.com</span>
      </li>
    </ul>
  </div>
</section>

<section class="card card--back" aria-label="Business card back">
  <div class="back-brand">
    <span class="back-brand__dot"></span>
    <p class="back-brand__name">GRANITE RIM SUPPLY, LLC</p>
  </div>
  <div class="services">
    <div class="services__group">
      <p class="services__heading">SPECIALIZING IN NEW AND USED TIRES &amp; WHEELS FOR</p>
      <p class="services__line services__line--italic">Loaders <span class="dot">•</span> Skid Steers <span class="dot">•</span> Telehandlers <span class="dot">•</span> Boom Lifts <span class="dot">•</span> Forklifs and more</p>
    </div>
    <div class="services__group">
      <p class="services__heading">ELIMINATING DOWNTIME</p>
      <p class="services__line">Wheel Exchange Program for New &amp; Used Foam Filled and Solid Rubber Tires</p>
    </div>
    <div class="services__group">
      <p class="services__heading">SPECIALTY SERVICES</p>
      <p class="services__line services__line--italic">Foam Filling Tires <span class="dot">•</span> Largest Tire Press in SE <span class="dot">•</span> ONSITE Forklift Tire Press</p>
      <p class="services__line services__line--italic">Boom Truck Services <span class="dot">•</span> Rubber Tracks</p>
    </div>
  </div>
</section>

</body>
</html>
```